International Clinical Software Company needs a new business card design

We are looking for a new business card design for our company that has recently expanded into the UK market, making us a multinational company.
After having rebranded our website and produced a new style guide, we are looking for a business card that is creative and attention grabbing, while being consistent with the style and colour scheme used on the new website, www.plumvora.example
We produce care management technology for the aged care market, but the main aspect we aim to communicate is the human element of our software, and the way it assists in providing better care for aged people, and stronger relationships between aged people and the staff that care for them.
Our current business card is a dark green with gold text, which makes the text quite difficult to read, not very aesthetically appealing and the colour scheme looks quite dated.
We would like something fresh and modern, that can still be colourful but doesn't use large blocks of dark colour, and uses the colours within our logo.
Something tying in with the leaves that are used in our logo could work quite nicely, along with the Autumn/Fall colours of soft greens, yellows and reds (also in our existing logo). However also happy to look at fresh, completely out of the box ideas we may not have yet considered.
Target Market(s)
The people that receive this business card work in the aged card or health industry and are either corporate/management level staff or clinical (Registered Nurses, care workers etc.)
Industry/Entity Type
Health Product
Contact Information for Business Card
Company Name - BrindlewayCare
Company locations: United Kingdom, Australia, New Zealand
Staff Details:
Staff name: Derek Mallow
Staff job title: Executive Chairman
Staff email: d.mallow@plumvora.example
Office phone number: 01742 918576
Font styles to use
Other font styles liked:
- Calibri
Requirements
Must have
- Must include the BrindlewayCare brand name in it's current font
- Must include logo (3 leaves in gold circle)
- Must include Business Card Details
Nice to have
- Elements of gold
- White space
- Something autumn themed but not too cliched
Should not have
- No blue - used by a major competitor and we would like to differentiate from them
- Large blocks of dark green colour (the green that appears in our leaves on the logo on our current business card is the background colour and it is far too dark)

```html
<!DOCTYPE html>
<html lang="en">
<head>
<meta charset="utf-8">
<title>BrindlewayCare Business Card</title>
<link rel="stylesheet" href="https://fonts.googleapis.com/css2?family=Source+Sans+3:wght@400;600&display=swap">
<style>
  :root {
    --backdrop: #8b8b8b;
    --card-white: #eeeff1;
    --gold: #9c8660;
    --gold-band: #a08a62;
    --crimson: #a3173f;
    --ink: #4a4a4a;
    --divider: #b9b9b9;
    --band-text: #f4efe4;
  }
  * { margin: 0; padding: 0; box-sizing: border-box; }
  html, body {
    width: 1105px;
    height: 1200px;
    overflow: hidden;
    background: var(--backdrop);
    font-family: "Source Sans 3", "Calibri", sans-serif;
  }
  .business-card {
    position: absolute;
    left: 52px;
    top: 313px;
    width: 1000px;
    height: 573px;
    background: var(--card-white);
    overflow: hidden;
  }
  .brand {
    position: absolute;
    left: 242px;
    top: 100px;
    display: flex;
    align-items: center;
    gap: 22px;
  }
  .brand-circle {
    width: 130px;
    height: 130px;
    border: 5px solid var(--gold);
    border-radius: 50%;
  }
  .brand-name {
    font-size: 58px;
    font-weight: 400;
    color: var(--gold);
    letter-spacing: 0.5px;
  }
  .person {
    position: absolute;
    right: 567px;
    top: 318px;
    text-align: right;
  }
  .person-name {
    font-size: 38px;
    font-weight: 600;
    color: var(--gold);
    line-height: 46px;
  }
  .person-title {
    font-size: 29px;
    font-weight: 400;
    color: var(--crimson);
    line-height: 36px;
  }
  .divider {
    position: absolute;
    left: 469px;
    top: 307px;
    width: 2px;
    height: 106px;
    background: var(--divider);
  }
  .contact-list {
    position: absolute;
    left: 512px;
    top: 300px;
    list-style: none;
  }
  .contact-item {
    display: flex;
    align-items: center;
    gap: 12px;
    height: 38px;
    font-size: 26px;
    color: var(--ink);
  }
  .contact-icon { width: 24px; height: 24px; fill: var(--gold); flex: none; }
  .footer-wave {
    position: absolute;
    left: 0;
    top: 420px;
    width: 1000px;
    height: 153px;
  }
  .locations {
    position: absolute;
    left: 0;
    right: 0;
    top: 525px;
    text-align: center;
    font-size: 27px;
    color: var(--band-text);
  }
</style>
</head>
<body>
  <div class="business-card">
    <div class="brand">
      <div class="brand-circle"></div>
      <div class="brand-name">BrindlewayCare</div>
    </div>

    <div class="person">
      <div class="person-name">Derek Mallow</div>
      <div class="person-title">Executive Chairman</div>
    </div>

    <div class="divider"></div>

    <ul class="contact-list">
      <li class="contact-item">
        <svg class="contact-icon" viewBox="0 0 24 24"><path d="M6.6 10.8c1.4 2.8 3.8 5.1 6.6 6.6l2.2-2.2c.3-.3.7-.4 1-.2 1.1.4 2.3.6 3.6.6.6 0 1 .4 1 1V20c0 .6-.4 1-1 1C10.6 21 3 13.4 3 4c0-.6.4-1 1-1h3.5c.6 0 1 .4 1 1 0 1.3.2 2.5.6 3.6.1.3 0 .7-.2 1l-2.3 2.2z"/></svg>
        <span>01742 918576</span>
      </li>
      <li class="contact-item">
        <svg class="contact-icon" viewBox="0 0 24 24"><path d="M2 5h20v14H2z M2 5l10 8 10-8" fill="var(--gold)"/><path d="M2 6l10 7.5L22 6" fill="none" stroke="var(--card-white)" stroke-width="1.6"/></svg>
        <span>d.mallow@plumvora.example</span>
      </li>
      <li class="contact-item">
        <svg class="contact-icon" viewBox="0 0 24 24"><circle cx="12" cy="12" r="10"/><path d="M2 12h20M12 2c3 3 3 17 0 20M12 2c-3 3-3 17 0 20" fill="none" stroke="var(--card-white)" stroke-width="1.4"/></svg>
        <span>www.plumvora.example</span>
      </li>
    </ul>

    <svg class="footer-wave" viewBox="0 0 1000 153" preserveAspectRatio="none">
      <path d="M0 20 C 300 65, 650 75, 1000 40 L1000 153 L0 153 Z" fill="var(--crimson)"/>
      <path d="M0 42 C 300 82, 650 88, 1000 44 L1000 153 L0 153 Z" fill="var(--card-white)"/>
      <path d="M0 50 C 300 90, 650 95, 1000 50 L1000 153 L0 153 Z" fill="var(--gold-band)"/>
    </svg>

    <div class="locations">United Kingdom | Australia | New Zealand</div>
  </div>
</body>
</html>
```